Equipment Finance Specialist I work with companies who need the funds to buy their equipment

I would like a business card that stands out on the shelves. I want to be able to hand it to someone and say WOW. This card should have my logo.
You can put color into it I am very open on design and color

What my company does is we deal with dealerships that sell equipment such as Dump Trucks garbage trucks tractors trailers. Customers get referred to us and depending on their time in business we will ask for the following items

Companies that have been in business for more than two years we have a credit application program up to 250K . With this program we need the following items Credit application filled out(which is what I would like to be able for the customer to click on my website to get.) as well as three current month bank statements.

Deals over 250k we will need the following items

2 years business tax returns
2 years personal tax returns
Profit & Loss statement
Personal Financial Statement

what we do
100% FINANCING
SEASONAL PAYMENTS
LOAN BALLOON PAYMENTS
TRAC LEASING
LOW-INTEREST REFINANCING RATES
DEBT CONSOLIDATION

We specialize in creative financing solutions and offer a variety of reliable, flexible and expandable lending choices.

Target Market(s)

Trucking Companies

Industry/Entity Type

Trucking Company

Contact Information for Business Card

* $250,000 Application only Program
* Loans from $30,000 to 5,000,000
* Competitive Interest Rates

Font styles to use
Serif
Sans Serif

Colors

Designer to choose colors to be used in the design.

Requirements
Must have
• On the back of the card.
• * $250,000 Application only Program
• * Loans from $30,000 to 5,000,000
• My name, email, website. address
• * Competitive Interest Rates
• * 100% Financing
Nice to have
• I want my logo to pop on the card
• My logo is the great one I would like to use
Should not have
• I am up for your creativity as well

```html
<!DOCTYPE html>
<html lang="en">
<head>
<meta charset="utf-8">
<title>Summit Lending Business Card</title>
<link href="https://fonts.googleapis.com/css2?family=Open+Sans:wght@400;600;700;800&display=swap" rel="stylesheet">
<style>
  :root {
    --navy: #12307a;
    --navy-deep: #0a1f5c;
    --navy-light: #1f47a3;
    --red: #d11f3a;
    --ink: #3d3d3d;
    --rule: #c9c9c9;
    --white: #ffffff;
    --stage: #2b2b2d;
  }
  * { box-sizing: border-box; margin: 0; padding: 0; }
  html, body { width: 1200px; height: 892px; overflow: hidden; }
  body {
    background: var(--stage);
    font-family: "Open Sans", Arial, sans-serif;
    position: relative;
  }
  .card {
    position: absolute;
    top: 292px;
    width: 540px;
    height: 308px;
    border-radius: 2px;
    overflow: hidden;
    box-shadow: 0 14px 30px rgba(0,0,0,0.45);
  }
  .brand {
    position: absolute;
    display: flex;
    align-items: center;
    gap: 10px;
  }
  .brand-dot {
    width: 26px; height: 26px;
    border-radius: 50%;
    flex: none;
  }
  .brand-name {
    font-weight: 800;
    letter-spacing: 0.5px;
    line-height: 1.05;
  }

  /* Back side */
  .card-back {
    left: 40px;
    background: linear-gradient(135deg, var(--navy-light) 0%, var(--navy) 45%, var(--navy-deep) 100%);
    color: var(--white);
  }
  .back-brand { left: 44px; top: 124px; }
  .back-brand .brand-dot { background: var(--white); }
  .back-brand .brand-name { font-size: 17px; color: var(--white); }
  .offer-list {
    position: absolute;
    left: 250px;
    top: 100px;
    list-style: none;
  }
  .offer-list li {
    font-weight: 600;
    font-size: 14.5px;
    line-height: 25px;
    position: relative;
    padding-left: 16px;
  }
  .offer-list li::before {
    content: "";
    position: absolute;
    left: 0; top: 10px;
    width: 6px; height: 6px;
    border-radius: 50%;
    background: var(--white);
  }

  /* Front side */
  .card-front {
    left: 620px;
    background: var(--white);
  }
  .front-brand { left: 72px; top: 120px; }
  .front-brand .brand-dot { width: 32px; height: 32px; background: var(--navy); }
  .front-brand .brand-name { font-size: 24px; color: var(--navy); }
  .divider {
    position: absolute;
    left: 292px;
    top: 44px;
    width: 1px;
    height: 170px;
    background: linear-gradient(var(--white), var(--rule) 30%, var(--rule) 70%, var(--white));
  }
  .contact {
    position: absolute;
    left: 312px;
    top: 52px;
    color: var(--ink);
  }
  .person-name {
    font-weight: 800;
    font-size: 19px;
    color: var(--navy);
    line-height: 22px;
  }
  .person-title {
    font-weight: 400;
    font-size: 13px;
    color: var(--red);
    line-height: 18px;
    margin-bottom: 10px;
  }
  .address {
    font-size: 12.5px;
    line-height: 18px;
    margin-bottom: 10px;
  }
  .contact-row {
    display: flex;
    align-items: center;
    gap: 9px;
    font-size: 12.5px;
    line-height: 19px;
  }
  .contact-row svg { width: 12px; height: 12px; fill: var(--navy); flex: none; }
  .accent-line {
    position: absolute;
    left: 0; right: 0;
    bottom: 44px;
    height: 2px;
    background: var(--red);
  }
  .accent-band {
    position: absolute;
    left: 0; right: 0;
    bottom: 0;
    height: 38px;
    background: var(--navy);
  }
</style>
</head>
<body>

  <section class="card card-back" aria-label="Card back">
    <div class="brand back-brand">
      <span class="brand-dot"></span>
      <span class="brand-name">SUMMIT<br>LENDING</span>
    </div>
    <ul class="offer-list">
      <li>$250,000 Application only Program</li>
      <li>Loans from $30,000 to 5,000,000</li>
      <li>Competitive Interest Rates</li>
      <li>100% Financing</li>
    </ul>
  </section>

  <section class="card card-front" aria-label="Card front">
    <div class="brand front-brand">
      <span class="brand-dot"></span>
      <span class="brand-name">SUMMIT<br>LENDING</span>
    </div>
    <div class="divider"></div>
    <div class="contact">
      <p class="person-name">MARK ELLISON</p>
      <p class="person-title">PRESIDENT</p>
      <p class="address">2710 Harbor Ridge Road<br>Lakeview, NY 11020</p>
      <p class="contact-row">
        <svg viewBox="0 0 24 24" aria-hidden="true"><path d="M6.6 10.8a15.1 15.1 0 0 0 6.6 6.6l2.2-2.2a1 1 0 0 1 1-.25 11.4 11.4 0 0 0 3.6.57 1 1 0 0 1 1 1V20a1 1 0 0 1-1 1A17 17 0 0 1 3 4a1 1 0 0 1 1-1h3.5a1 1 0 0 1 1 1c0 1.25.2 2.45.57 3.57a1 1 0 0 1-.25 1z"/></svg>
        555 0192 4408
      </p>
      <p class="contact-row">
        <svg viewBox="0 0 24 24" aria-hidden="true"><path d="M2 5h20v14H2z M2 5l10 8 10-8" /></svg>
        mark@summitlending.com
      </p>
      <p class="contact-row">
        <svg viewBox="0 0 24 24" aria-hidden="true"><circle cx="12" cy="12" r="10"/></svg>
        www.summitlending.com
      </p>
    </div>
    <div class="accent-line"></div>
    <div class="accent-band"></div>
  </section>

</body>
</html>
```